Norrell Advisory WA Business Card

Create an interesting, eye catching and colourful two sided business card. We are a business consulting operation assisting SME's improve all areas of their business. We provide consulting services to assist SME's to create a culture of continuous improvement, making a positive difference in the business. Our tag line is Small changes, big rewards. We want to create a well recognised, innovative brand that can be continued throughout our website, social media and email correspondence.

Target Market(s)

Small to Medium Enterprise Business Owners

Industry/Entity Type

Business Consultant

Contact Information for Business Card

Name of Business: Norrell Advisory - Steady Steps Lasting Gains
Derek Holloway Ph 0407385510 Megan Holloway Ph 0407913847
Email norrelladvisorywa@mailbox-example.com
Web address TBA
FaceBook page TBA

BACKSIDE OF CARD

Providing assistance with:

• Organisation & Efficiency
• Revenue generation & Marketing
• Financial Management
• Production quality & delivery
• Systems & Process documentation
• Exit Strategy

Font styles to use
Other font styles liked:
• Calibri

Colors

Designer to choose colors to be used in the design.

Requirements
Must have
• Calibri font

```html
<!DOCTYPE html>
<html lang="en">
<head>
<meta charset="utf-8">
<title>Norrell Advisory WA Business Card</title>
<link rel="stylesheet" href="https://fonts.googleapis.com/css2?family=Open+Sans:wght@400;600;700&display=swap">
<style>
  :root {
    --stage: #3a3a3c;
    --card-light: #ffffff;
    --card-dark: #2a2a2a;
    --ink: #2b2b2b;
    --ink-soft: #4a4a4a;
    --on-dark: #e6e6e6;
    --rule: #cfcfcf;
    --rule-dark: #6a6a6a;
    --yellow: #f6b21f;
    --blue: #1a86cc;
    --red: #e63f2e;
    --green: #77bb35;
  }
  * { box-sizing: border-box; margin: 0; padding: 0; }
  html, body { width: 1200px; height: 896px; overflow: hidden; }
  body {
    background: var(--stage);
    font-family: "Open Sans", sans-serif;
    position: relative;
  }
  .card {
    position: absolute;
    left: 240px;
    width: 720px;
    height: 412px;
    overflow: hidden;
    box-shadow: 0 10px 30px rgba(0,0,0,.35);
  }
  .card--front { top: 26px; background: var(--card-light); color: var(--ink); }
  .card--back  { top: 458px; background: var(--card-dark); color: var(--on-dark); }

  .colour-band {
    position: absolute; left: 0; right: 0; bottom: 0; height: 12px;
    display: flex;
  }
  .colour-band span { flex: 1; }
  .colour-band .yellow { background: var(--yellow); }
  .colour-band .blue { background: var(--blue); }
  .colour-band .red { background: var(--red); }
  .colour-band .green { background: var(--green); }

  /* Front */
  .brand {
    position: absolute; right: 46px; top: 120px;
    display: flex; align-items: center; gap: 16px;
  }
  .brand__mark { width: 34px; height: 34px; background: var(--blue); }
  .brand__name {
    font-weight: 700; font-size: 33px; letter-spacing: 1px;
    text-transform: uppercase; color: var(--ink);
  }
  .people {
    position: absolute; left: 46px; top: 196px;
    display: flex; gap: 48px;
  }
  .person__name {
    font-weight: 700; font-size: 24px; text-transform: uppercase;
    letter-spacing: .5px; color: var(--ink);
  }
  .person__phone {
    display: flex; align-items: center; gap: 6px;
    font-size: 17px; color: var(--ink-soft); margin-top: 2px;
  }
  .person__phone svg { width: 12px; height: 17px; }
  .contact {
    position: absolute; left: 46px; top: 290px;
    font-size: 17px; color: var(--ink-soft); line-height: 1.4;
  }
  .contact__web { color: var(--yellow); }
  .contact__web .blue { color: var(--blue); }
  .contact__web .red { color: var(--red); }
  .contact__web .green { color: var(--green); }
  .contact__rule {
    position: absolute; left: 46px; right: 46px; top: 358px;
    height: 1px; background: var(--rule);
  }

  /* Back */
  .back__name {
    position: absolute; left: 0; right: 0; top: 66px; text-align: center;
    font-weight: 700; font-size: 44px; letter-spacing: 1.5px;
    text-transform: uppercase; color: var(--on-dark);
  }
  .tagline {
    position: absolute; left: 0; right: 0; top: 128px; text-align: center;
    font-weight: 600; font-size: 17px; text-transform: uppercase; letter-spacing: .5px;
  }
  .tagline .yellow { color: var(--yellow); }
  .tagline .blue { color: var(--blue); }
  .tagline .red { color: var(--red); }
  .tagline .green { color: var(--green); }
  .services__heading {
    position: absolute; left: 60px; right: 60px; top: 184px;
    display: flex; align-items: center; gap: 14px;
    font-weight: 600; font-size: 17px; text-transform: uppercase; letter-spacing: .5px;
    color: var(--on-dark); white-space: nowrap;
  }
  .services__heading::before,
  .services__heading::after {
    content: ""; flex: 1; height: 1px; background: var(--rule-dark);
  }
  .services__list {
    position: absolute; left: 0; right: 0; top: 226px;
    list-style: none; text-align: center;
    font-size: 19px; line-height: 1.55; color: var(--on-dark);
  }
</style>
</head>
<body>
  <section class="card card--front" aria-label="Card front">
    <div class="brand">
      <span class="brand__mark" aria-hidden="true"></span>
      <span class="brand__name">Norrell Advisory</span>
    </div>
    <div class="people">
      <div class="person">
        <div class="person__name">Derek Holloway</div>
        <div class="person__phone">
          <svg viewBox="0 0 12 17" aria-hidden="true"><path d="M3 1 L5 1 L6 5 L4 6 Q4 10 7 12 L9 11 L11 14 L9 16 Q1 13 1 4 Z" fill="var(--blue)"/></svg>
          0407385510
        </div>
      </div>
      <div class="person">
        <div class="person__name">Megan Holloway</div>
        <div class="person__phone">
          <svg viewBox="0 0 12 17" aria-hidden="true"><path d="M3 1 L5 1 L6 5 L4 6 Q4 10 7 12 L9 11 L11 14 L9 16 Q1 13 1 4 Z" fill="var(--blue)"/></svg>
          0407913847
        </div>
      </div>
    </div>
    <div class="contact">
      <div>norrelladvisorywa@mailbox-example.com | <span class="contact__web">www.<span class="blue">norrell</span><span class="red">advisory</span><span class="green">.com</span></span></div>
      <div>social.norrelladvisory.com</div>
    </div>
    <div class="contact__rule"></div>
    <div class="colour-band" aria-hidden="true"><span class="yellow"></span><span class="blue"></span><span class="red"></span><span class="green"></span></div>
  </section>

  <section class="card card--back" aria-label="Card back">
    <h1 class="back__name">Norrell Advisory</h1>
    <p class="tagline"><span class="yellow">Steady</span> <span class="blue">Steps</span> <span class="red">Lasting</span> <span class="green">Gains</span></p>
    <h2 class="services__heading">Providing assistance with</h2>
    <ul class="services__list">
      <li>Organisation &amp; Efficiency • Revenue generation &amp; Marketing</li>
      <li>Financial Management • Production quality &amp; delivery</li>
      <li>Systems &amp; Process documentation • Exit Strategy</li>
    </ul>
    <div class="colour-band" aria-hidden="true"><span class="yellow"></span><span class="blue"></span><span class="red"></span><span class="green"></span></div>
  </section>
</body>
</html>
```